holloway paving service

Needs to have phone number 0418259730 and email markholloway@brightmail.com.au.
ABN 62318470915
name mark holloway

For all your concreting solutions
Excavation
Exposed & colour concrete
House & shed slabs
Driveways
Landing & steps

Contact Information for Business Card

ph 0418259730
email markholloway@brightmail.com.au.
ABN 62318470915
name mark holloway

```html
<!DOCTYPE html>
<html lang="en">
<head>
<meta charset="utf-8">
<title>Holloway Paving Service – Business Card</title>
<link href="https://fonts.googleapis.com/css2?family=Arimo:wght@400;700&display=swap" rel="stylesheet">
<style>
  :root {
    --bg: #dcdcdc;
    --card: #ffffff;
    --orange: #f26722;
    --grey: #5f5f5f;
    --white: #ffffff;
  }
  * { margin: 0; padding: 0; box-sizing: border-box; }
  html, body { width: 1200px; height: 900px; overflow: hidden; }
  body {
    background: var(--bg);
    font-family: "Arimo", Arial, sans-serif;
    display: flex;
    flex-direction: column;
    align-items: center;
    justify-content: center;
    gap: 44px;
  }
  .card {
    position: relative;
    width: 630px;
    height: 360px;
    background: var(--card);
    box-shadow: 0 6px 18px rgba(0,0,0,0.18);
    overflow: hidden;
  }

  /* Back face */
  .card-back {
    display: flex;
    flex-direction: column;
    align-items: center;
    justify-content: center;
    gap: 10px;
  }
  .brand {
    display: flex;
    align-items: center;
    gap: 10px;
    color: var(--orange);
    font-weight: 700;
    text-transform: uppercase;
    letter-spacing: 0.02em;
  }
  .brand-mark {
    width: 22px; height: 22px;
    background: var(--orange);
  }
  .card-back .brand { font-size: 26px; }
  .brand-rule {
    width: 300px; height: 2px; background: var(--grey); opacity: 0.5;
  }

  /* Front face */
  .front-shape { position: absolute; inset: 0; }
  .identity {
    position: absolute;
    left: 42px; top: 40px;
    color: var(--orange);
  }
  .identity .name { font-size: 24px; font-weight: 700; line-height: 1.1; }
  .identity .abn { font-size: 17px; margin-top: 3px; }
  .card-front .brand {
    position: absolute;
    left: 42px; top: 150px;
    font-size: 19px;
    width: 250px;
    flex-wrap: nowrap;
  }
  .services {
    position: absolute;
    left: 410px; top: 34px;
    list-style: none;
    color: var(--white);
    font-size: 15px;
    line-height: 1.45;
  }
  .services li::before {
    content: "";
    display: inline-block;
    width: 6px; height: 6px;
    background: var(--white);
    margin-right: 8px;
    vertical-align: middle;
  }
  .contact {
    position: absolute;
    left: 42px; bottom: 46px;
    list-style: none;
    color: var(--orange);
    font-size: 20px;
    line-height: 1.45;
  }
  .contact li { display: flex; align-items: center; gap: 10px; }
  .contact svg { width: 20px; height: 16px; fill: var(--orange); flex: none; }
</style>
</head>
<body>

<section class="card card-back" aria-label="Business card back">
  <div class="brand"><span class="brand-mark"></span><span>Holloway Paving Service</span></div>
  <div class="brand-rule"></div>
</section>

<section class="card card-front" aria-label="Business card front">
  <svg class="front-shape" viewBox="0 0 630 360" preserveAspectRatio="none" aria-hidden="true">
    <polygon points="300,165 395,0 630,0 630,205 520,245" fill="var(--orange)"/>
  </svg>

  <div class="identity">
    <p class="name">mark holloway</p>
    <p class="abn">ABN 62318470915</p>
  </div>

  <div class="brand"><span class="brand-mark"></span><span>Holloway Paving</span></div>

  <ul class="services">
    <li>For all your concreting solutions</li>
    <li>Excavation</li>
    <li>Exposed &amp; colour concrete</li>
    <li>House &amp; shed slabs</li>
    <li>Driveways</li>
    <li>Landing &amp; steps</li>
  </ul>

  <ul class="contact">
    <li>
      <svg viewBox="0 0 20 16" aria-hidden="true"><rect x="0" y="3" width="20" height="13" rx="2"/><rect x="4" y="0" width="12" height="4" rx="1"/></svg>
      <span>0418259730</span>
    </li>
    <li>
      <svg viewBox="0 0 20 16" aria-hidden="true"><path d="M0 2h20v12H0z M1.5 3.5 10 9.5l8.5-6" fill="none" stroke="var(--orange)" stroke-width="2"/></svg>
      <span>markholloway@brightmail.com.au.</span>
    </li>
  </ul>
</section>

</body>
</html>
```